Structural Engineering Business Card

Brookvane Drafting does residential house plans for clients in Central Florida. Would like simple but elegant business card that is appropriate for a house plan engineering company. Prefer black business card with black/white them but open to other shades of blue. I uploaded a sample card that I came across that looked good but please come up with your own creative designs.

Contact Information for Business Card

Name, Title, Phone, Email, Address, website

```html
<!DOCTYPE html>
<html lang="en">
<head>
<meta charset="utf-8">
<title>Brookvane Drafting – Business Card</title>
<link href="https://fonts.googleapis.com/css2?family=Poppins:wght@400;700;800&display=swap" rel="stylesheet">
<style>
  :root {
    --ink: #0a0a0a;
    --paper: #ffffff;
    --stage: #e6e6e4;
    --rule: #6b6b6b;
    --pattern-dark: #050505;
    --pattern-mid: #2a2a2a;
  }
  * { box-sizing: border-box; margin: 0; padding: 0; }
  html, body {
    width: 1200px; height: 900px; overflow: hidden;
    background: var(--stage);
    font-family: "Poppins", sans-serif;
  }
  .stage { position: relative; width: 1200px; height: 900px; }
  .card {
    position: absolute; width: 630px; height: 360px;
    box-shadow: 0 10px 28px rgba(0,0,0,0.25);
    overflow: hidden;
  }
  /* Back face */
  .card-back { left: 200px; top: 60px; background: var(--ink); }
  .back-pattern {
    position: absolute; inset: 0;
    background: linear-gradient(160deg, var(--pattern-mid) 0%, var(--pattern-dark) 55%, var(--ink) 100%);
  }
  .back-brand {
    position: absolute; left: 50%; top: 50%;
    transform: translate(-50%, -50%);
    display: flex; align-items: center; gap: 10px;
    color: var(--paper); font-weight: 800; font-size: 24px;
    text-transform: uppercase; letter-spacing: 0.5px; white-space: nowrap;
  }
  .brand-square { width: 16px; height: 16px; background: currentColor; flex: none; }

  /* Front face */
  .card-front { left: 370px; top: 480px; background: var(--paper); color: var(--ink); }
  .front-brand {
    position: absolute; left: 34px; top: 128px; width: 260px;
    display: flex; align-items: center; gap: 10px;
    font-weight: 800; font-size: 27px; line-height: 1.05;
    text-transform: uppercase;
  }
  .front-brand .brand-square { width: 20px; height: 20px; }
  .divider {
    position: absolute; left: 318px; top: 52px; width: 1px; height: 190px;
    background: var(--rule);
  }
  .contact { position: absolute; left: 342px; top: 50px; width: 270px; }
  .person-name { font-weight: 700; font-size: 21px; line-height: 1.1; text-transform: uppercase; }
  .person-title { font-size: 13px; margin-bottom: 12px; }
  .contact-list { list-style: none; font-size: 13px; line-height: 1.6; }
  .contact-list li { display: flex; align-items: center; gap: 9px; }
  .contact-list svg { width: 14px; height: 14px; flex: none; }
  .address { font-size: 13px; line-height: 1.35; margin-top: 12px; padding-left: 23px; }
  .wave { position: absolute; left: 0; bottom: 0; width: 630px; height: 130px; }
</style>
</head>
<body>
<main class="stage">

  <section class="card card-back" aria-label="Card back">
    <div class="back-pattern" role="img" aria-label="Repeating tonal brand pattern in dark greys"></div>
    <div class="back-brand"><span class="brand-square"></span>Brookvane Drafting</div>
  </section>

  <section class="card card-front" aria-label="Card front">
    <div class="front-brand"><span class="brand-square"></span><span>Brookvane Drafting</span></div>
    <div class="divider"></div>

    <div class="contact">
      <p class="person-name">Daniel Reyes</p>
      <p class="person-title">Managing Director</p>
      <ul class="contact-list">
        <li>
          <svg viewBox="0 0 24 24" aria-hidden="true"><path fill="currentColor" d="M6.6 10.8a15.1 15.1 0 0 0 6.6 6.6l2.2-2.2a1 1 0 0 1 1-.25 11.4 11.4 0 0 0 3.6.57 1 1 0 0 1 1 1V20a1 1 0 0 1-1 1A17 17 0 0 1 3 4a1 1 0 0 1 1-1h3.5a1 1 0 0 1 1 1c0 1.25.2 2.45.57 3.6a1 1 0 0 1-.25 1z"/></svg>
          044-555 018 273
        </li>
        <li>
          <svg viewBox="0 0 24 24" aria-hidden="true"><path fill="currentColor" d="M2 5h20v14H2zm2 2v.5l8 5 8-5V7l-8 5z"/></svg>
          info@brookvane.com
        </li>
        <li>
          <svg viewBox="0 0 24 24" aria-hidden="true"><g fill="none" stroke="currentColor" stroke-width="2"><circle cx="12" cy="12" r="9"/><path d="M3 12h18M12 3c3 3.5 3 14.5 0 18M12 3c-3 3.5-3 14.5 0 18"/></g></svg>
          www.brookvane.com
        </li>
      </ul>
      <p class="address">418 Cedar Hollow Lane<br>Orlando, FL 32801</p>
    </div>

    <svg class="wave" viewBox="0 0 630 130" preserveAspectRatio="none" aria-hidden="true">
      <path fill="var(--ink)" d="M0 70 C 120 50, 230 130, 380 90 C 480 62, 560 20, 630 12 L630 130 L0 130 Z"/>
    </svg>
  </section>

</main>
</body>
</html>
```